2020-23 Strategic Plan - Graphic Design Work

We would would like to have our strategic plan designed. It should be two pages.

- I am looking for suggestions on ways to lay this out. I don’t like this boxy layout. It was great for the committee as we went through multiple versions, but I’d prefer the final not follow this boxy format

- I’ve included a few images we own (feel free to use any or none of them). Also attached our logo.

- Have a look at our new website to see our new branding look and feel (launching next week) https://ourvelmora.hostpage-qx.net/

- I've included a copy of our logo.

Target Market(s)

Membership

Other font styles liked:
• Lato

Requirements
Must have
• Excellent layout. Easy to ready. Consistent with branding.

```html
<!DOCTYPE html>
<html lang="en">
<head>
<meta charset="utf-8">
<title>ICV 2020-2023 Strategic Plan</title>
<link rel="stylesheet" href="https://fonts.googleapis.com/css2?family=Montserrat:ital,wght@0,400;0,500;0,600;0,700;0,800;0,900;1,500;1,700&family=Raleway:ital,wght@0,400;0,500;1,500&display=swap">
<style>
:root{
  --bg:#ebecee;
  --paper:#ffffff;
  --green:#4a9a3f;
  --green-dark:#0b4a2a;
  --red:#e3232d;
  --grey-band:#eef0f2;
  --ink:#3a3a3a;
  --muted:#5a5a5a;
}
*{margin:0;padding:0;box-sizing:border-box}
html,body{width:890px;height:1200px;overflow:hidden;background:var(--bg)}
.stage{position:relative;width:890px;height:1200px;background:var(--bg);overflow:hidden}
.page{position:absolute;width:662px;height:937px;background:var(--paper);transform-origin:0 0;transform:scale(.5388);overflow:hidden;font-family:Raleway,sans-serif;color:var(--ink)}
.p1{left:71px;top:68.4px}.p2{left:455.3px;top:68.4px}.p3{left:71px;top:626.6px}.p4{left:455.3px;top:626.6px}
.abs{position:absolute}

/* cover */
.brand{position:absolute;left:50px;top:46px;color:var(--green-dark);font-family:Montserrat,sans-serif;font-weight:800;display:flex;align-items:center;gap:10px}
.brand-mark{width:26px;height:26px;background:var(--green)}
.brand-name{font-size:17px;line-height:1.15;letter-spacing:.5px}
.site{position:absolute;left:395px;top:70px;font-family:Montserrat,sans-serif;font-weight:500;font-size:15.5px;color:var(--green-dark)}
.hero{position:absolute;left:0;top:158px;width:662px;height:326px;background:linear-gradient(115deg,#1d3a6e 0%,#5a6fa8 28%,#b58aa8 48%,#6b5f8e 64%,#203a5c 82%,#4b3a52 100%)}
.year{position:absolute;left:47px;top:270px;font-family:Montserrat,sans-serif;font-weight:500;font-size:58px;color:#fff;letter-spacing:1px}
.plan-title{position:absolute;left:46px;top:334px;font-family:Montserrat,sans-serif;font-weight:800;font-size:61px;color:#fff;letter-spacing:-.5px;white-space:nowrap}
.quote-red{position:absolute;left:48px;top:415px;width:82px;height:187px;background:var(--red)}
.quote-red span{position:absolute;left:18px;top:58px;font-family:Montserrat,sans-serif;font-weight:900;font-size:64px;color:#fff}
.intro{position:absolute;left:142px;top:415px;width:474px;height:187px;background:var(--green);color:#fff;font-family:Montserrat,sans-serif;font-style:italic;font-weight:500;font-size:13.3px;line-height:17.4px;padding:13px 14px 0 15px;text-align:justify}
.col-head{position:absolute;top:630px;font-family:Montserrat,sans-serif;font-weight:800;font-size:38px}
.col-text{position:absolute;top:684px;font-size:12.4px;line-height:14.7px;color:var(--ink)}
.foot{position:absolute;left:0;top:880px}

/* pillar page */
.band{position:absolute;left:0;width:662px;background:var(--grey-band)}
.kicker{position:absolute;left:38px;font-family:Montserrat,sans-serif;font-weight:600;font-size:12px;letter-spacing:1.2px;color:var(--muted)}
.pillar{position:absolute;left:36px;font-family:Montserrat,sans-serif;font-weight:900;font-size:48px;letter-spacing:4px;line-height:1}
.rule{position:absolute;left:310px;width:352px;height:8px;background:var(--green)}
.h{position:absolute;font-family:Montserrat,sans-serif;font-weight:700;font-size:12.5px;line-height:14px;letter-spacing:1.2px;color:var(--green)}
.t{position:absolute;font-size:8.6px;line-height:10.6px;color:var(--ink)}
.t p{margin-bottom:10px}
.c1{left:38px;width:155px}.c2{left:223px;width:200px}.c3{left:454px;width:178px}

/* table page */
.thead{position:absolute;left:0;top:0;width:662px;height:85px;background:var(--green)}
.th{position:absolute;top:38px;font-family:Montserrat,sans-serif;font-weight:700;font-size:12px;line-height:14px;color:#fff}
.side{position:absolute;top:85px;width:22px;height:155px;background:var(--green)}
.label{position:absolute;left:23px;width:75px;display:flex;align-items:center;justify-content:center}
.label span{transform:rotate(-90deg);font-family:Montserrat,sans-serif;font-weight:800;font-size:16px;letter-spacing:3px;white-space:nowrap}
.cell{position:absolute;left:117px;width:527px}
.q{position:absolute;left:31px;font-family:Montserrat,sans-serif;font-weight:900;font-size:28px;line-height:1}
.obj{position:absolute;left:31px;width:128px;font-family:Montserrat,sans-serif;font-style:italic;font-weight:700;font-size:12px;line-height:14.8px}
.g{position:absolute;left:195px;width:135px;font-size:9.6px;line-height:12px}
.a{position:absolute;left:361px;width:150px;font-size:9.6px;line-height:12px}
.g p,.a p{margin-bottom:11px}
.light{background:var(--grey-band);color:var(--ink)}
.dark{background:var(--green-dark);color:#fff}
.mid{background:var(--green);color:#fff}
</style>
</head>
<body>
<div class="stage">

  <!-- cover, set one -->
  <section class="page p1">
    <div class="brand"><span class="brand-mark"></span><span class="brand-name">INSTITUTE OF<br>CIVIC VALUERS</span></div>
    <div class="site">www.ourvelmora.hostpage-qx.net</div>
    <div class="hero" role="img" aria-label="Upward view of city skyscrapers against a streaked dusk sky"></div>
    <div class="year">2020-2023</div>
    <div class="plan-title">STRAGETIC PLAN</div>
    <div class="quote-red"><span>“</span></div>
    <div class="intro">With over 1,250 members, the Institute of Civic Valuers is Canada’s largest association of property assessment and taxation professionals. Our diverse membership is comprised of individuals from the private and public sectors practicing in the fields of assessment, consultancy, appraisal, taxation and law. Incorporated in May 1957, the ICV is dedicated to advancing the interests, education and professional competence of its members. Our members are highly qualified and widely recognized as the leading professionals in the property assessment industry.</div>
    <div class="col-head" style="left:47px;color:var(--green)">Vision</div>
    <div class="col-head" style="left:230px;color:var(--green-dark)">Mission</div>
    <div class="col-head" style="left:436px;color:#2f4a3c">Values</div>
    <div class="col-text" style="left:47px;width:165px">To be the industry leaderin education, ethical standards, and professional accreditation in the field of property assessment in Canada.</div>
    <div class="col-text" style="left:230px;width:180px">To provide specialized education through a comprehensive approach to training which embraces all available technologies. To promote professional development and to ensure our members are recognized as experts in the field of property assessment and related functions.</div>
    <div class="col-text" style="left:437px;width:190px">The Institute of Civic Valuers and its members value professionalism, inclusivity, diversity, integrity, ethics, accountability, and expertise. The ICV is committed to serving all members and stakeholders with competence and respect, rejecting all forms of prejudice and discrimination</div>
    <svg class="foot" width="662" height="57" viewBox="0 0 662 57">
      <polygon points="0,5 245,5 275,27 662,27 662,57 0,57" fill="var(--green-dark)"/>
      <rect x="265" y="13" width="397" height="6" fill="var(--green)"/>
    </svg>
  </section>

  <!-- pillars, set one -->
  <section class="page p2">
    <div class="band" style="top:62px;height:208px"></div>
    <div class="band" style="top:495px;height:200px"></div>

    <div class="kicker" style="top:38px">STRATEGIC PILLAR</div>
    <div class="pillar" style="top:52px;color:var(--green)">EDUCATE</div>
    <div class="rule" style="top:64px"></div>
    <div class="h c1" style="top:107px">STRATEGIC<br>OBJECTIVE</div>
    <div class="h c2" style="top:107px">STRATEGIC<br>GOALS</div>
    <div class="h c3" style="top:107px">SAMPLE SUPPORTING<br>ACTIONS</div>
    <div class="t c1" style="top:142px">Be the most trusted, relevant, and accessible provider of education and credentials in the field of property assessment in Canada</div>
    <div class="t c2" style="top:142px"><p>Ensure a catalogue of relevant, high-quality courses, which meet the evolving needs of assessment professionals</p><p>Provide an equal ICV member experience and service, regardless of geography</p></div>
    <div class="t c3" style="top:142px"><p>Utilize technology to offer interactive and accessible online events</p><p>Develop provincial legislation-specific content for ICV courses</p><p>Lead opportunities for collaboration across districts to increase access to quality PD opportunities</p></div>

    <div class="kicker" style="top:259px">STRATEGIC PILLAR</div>
    <div class="pillar" style="top:272px;color:var(--green-dark)">GROW</div>
    <div class="h c1" style="top:328px">STRATEGIC<br>OBJECTIVE</div>
    <div class="h c2" style="top:328px">STRATEGIC<br>GOALS</div>
    <div class="h c3" style="top:328px">SAMPLE SUPPORTING<br>ACTIONS</div>
    <div class="t c1" style="top:364px">Increase the ICV’s membership by serving all career levels and forging strong strategic partnerships.</div>
    <div class="t c2" style="top:364px"><p>Enhance opportunities for senior assessment professionals through the FICV designation.</p><p>Connect with young professionals by enhancing member communications, improving member onboarding, and expanding scholarship opportunities.</p></div>
    <div class="t c3" style="top:364px"><p>Develop framework for a specialist designation track</p><p>Work collaboratively with strategic partners from across the country to develop criteria for, and launch, the FICV designation</p><p>Redesign the new member onboarding experience</p></div>

    <div class="kicker" style="top:469px">STRATEGIC PILLAR</div>
    <div class="pillar" style="top:482px;color:var(--green)">LEAD</div>
    <div class="rule" style="top:490px"></div>
    <div class="h c1" style="top:539px">STRATEGIC<br>OBJECTIVE</div>
    <div class="h c2" style="top:539px">STRATEGIC<br>GOALS</div>
    <div class="h c3" style="top:539px">SAMPLE SUPPORTING<br>ACTIONS</div>
    <div class="t c1" style="top:572px">Strengthen the reputation of the organization and its members by acting as a leader within the field of property assessment in Canada</div>
    <div class="t c2" style="top:572px"><p>Embrace the role of leader and advocate within the property assessment profession.</p><p>Strengthen current, and develop new, strategic partnerships with peer associations across Canada.</p></div>
    <div class="t c3" style="top:572px"><p>Adopt an advocacy voice for the assessment profession to ensure interests are being represented</p><p>Work with strategic partners to produce industry white papers with national relevance</p><p>Engage with various levels of government across Canada</p></div>

    <div class="kicker" style="top:686px">STRATEGIC PILLAR</div>
    <div class="pillar" style="top:699px;color:var(--green-dark)">GOVERN</div>
    <div class="h c1" style="top:753px">STRATEGIC<br>OBJECTIVE</div>
    <div class="h c2" style="top:753px">STRATEGIC<br>GOALS</div>
    <div class="h c3" style="top:753px">SAMPLE SUPPORTING<br>ACTIONS</div>
    <div class="t c1" style="top:788px">Fortify the future of the ICV through operational excellence and a diverse group of talented volunteers</div>
    <div class="t c2" style="top:788px"><p>Review and align association management practices with strategic objectives and statements of Vision, Mission and Values.</p><p>Secure the ICV’s financial stability by reviewing current pricing model and practicing sound risk management.</p></div>
    <div class="t c3" style="top:788px"><p>Align the ICV budget and staffing needs to achieve clear strategic objectives</p><p>Utilize automation to modernize systems and administrative processes</p><p>Review and assess the relevance of current committees to determine if sufficient to meet the requirements of the strategic plan, and create new committees if deemed relevant</p></div>
  </section>

  <!-- cover, set two -->
  <section class="page p3">
    <div class="brand"><span class="brand-mark"></span><span class="brand-name">INSTITUTE OF<br>CIVIC VALUERS</span></div>
    <div class="site">www.ourvelmora.hostpage-qx.net</div>
    <div class="hero" role="img" aria-label="Upward view of city skyscrapers against a streaked dusk sky"></div>
    <div class="year">2020-2023</div>
    <div class="plan-title">STRAGETIC PLAN</div>
    <div class="quote-red"><span>“</span></div>
    <div class="intro">With over 1,250 members, the Institute of Civic Valuers is Canada’s largest association of property assessment and taxation professionals. Our diverse membership is comprised of individuals from the private and public sectors practicing in the fields of assessment, consultancy, appraisal, taxation and law. Incorporated in May 1957, the ICV is dedicated to advancing the interests, education and professional competence of its members. Our members are highly qualified and widely recognized as the leading professionals in the property assessment industry.</div>
    <div class="col-head" style="left:47px;color:var(--green)">Vision</div>
    <div class="col-head" style="left:230px;color:var(--green-dark)">Mission</div>
    <div class="col-head" style="left:436px;color:#2f4a3c">Values</div>
    <div class="col-text" style="left:47px;width:165px">To be the industry leaderin education, ethical standards, and professional accreditation in the field of property assessment in Canada.</div>
    <div class="col-text" style="left:230px;width:180px">To provide specialized education through a comprehensive approach to training which embraces all available technologies. To promote professional development and to ensure our members are recognized as experts in the field of property assessment and related functions.</div>
    <div class="col-text" style="left:437px;width:190px">The Institute of Civic Valuers and its members value professionalism, inclusivity, diversity, integrity, ethics, accountability, and expertise. The ICV is committed to serving all members and stakeholders with competence and respect, rejecting all forms of prejudice and discrimination</div>
    <svg class="foot" width="662" height="57" viewBox="0 0 662 57">
      <polygon points="0,5 245,5 275,27 662,27 662,57 0,57" fill="var(--green-dark)"/>
      <rect x="265" y="13" width="397" height="6" fill="var(--green)"/>
    </svg>
  </section>

  <!-- pillar table, set two -->
  <section class="page p4">
    <div class="thead"></div>
    <div class="side" style="left:0"></div>
    <div class="side" style="left:644px;width:18px"></div>
    <div class="th" style="left:33px">STRATEGIC<br>PILLAR</div>
    <div class="th" style="left:148px">STRATEGIC<br>OBJECTIVE</div>
    <div class="th" style="left:312px">STRATEGIC<br>GOALS</div>
    <div class="th" style="left:478px">SAMPLE SUPPORTING<br>ACTIONS</div>

    <div class="label light" style="top:85px;height:193px"><span style="color:var(--green)">EDUCATE</span></div>
    <div class="cell light" style="top:85px;height:193px">
      <div class="q" style="top:22px;color:var(--green-dark)">“</div>
      <div class="obj" style="top:55px;color:var(--green-dark)">Be the most trusted, relevant, and accessible provider of education and credentials in the field of property assessment in Canada</div>
      <div class="g" style="top:27px"><p>Ensure a catalogue of relevant, high-quality courses, which meet the evolving needs of assessment professionals</p><p>Provide an equal ICV member experience and service, regardless of geography</p></div>
      <div class="a" style="top:27px"><p>Utilize technology to offer interactive and accessible online events</p><p>Develop provincial legislation-specific content for ICV courses</p><p>Lead opportunities for collaboration across districts to increase access to quality PD opportunities</p></div>
    </div>

    <div class="label dark" style="top:298px;height:185px"><span>GROW</span></div>
    <div class="cell dark" style="top:298px;height:185px">
      <div class="q" style="top:24px;color:var(--green)">“</div>
      <div class="obj" style="top:68px">Increase the ICV’s membership by serving all career levels and forging strong strategic partnerships.</div>
      <div class="g" style="top:28px"><p>Enhance opportunities for senior assessment professionals through the FICV designation.</p><p>Connect with young professionals by enhancing member communications, improving member onboarding, and expanding scholarship opportunities.</p></div>
      <div class="a" style="top:28px"><p>Develop framework for a specialist designation track</p><p>Work collaboratively with strategic partners from across the country to develop criteria for, and launch, the FICV designation</p><p>Redesign the new member onboarding experience</p></div>
    </div>

    <div class="label light" style="top:510px;height:190px"><span style="color:var(--green-dark)">LEAD</span></div>
    <div class="cell light" style="top:510px;height:190px">
      <div class="q" style="top:22px;color:var(--green)">“</div>
      <div class="obj" style="top:56px;color:var(--green-dark)">Strengthen the reputation of the organization and its members by acting as a leader within the field of property assessment in Canada</div>
      <div class="g" style="top:26px"><p>Embrace the role of leader and advocate within the property assessment profession</p><p>Strengthen current, and develop new, strategic partnerships with peer associations across Canada.</p></div>
      <div class="a" style="top:26px"><p>Adopt an advocacy voice for the assessment profession to ensure interests are being represented</p><p>Work with strategic partners to produce industry white papers with national relevance</p><p>Engage with various levels of government across Canada</p></div>
    </div>

    <div class="label mid" style="top:722px;height:196px"><span>GOVERN</span></div>
    <div class="cell mid" style="top:722px;height:196px">
      <div class="q" style="top:14px;color:var(--green-dark)">“</div>
      <div class="obj" style="top:62px">Fortify the future of the ICV through operational excellence and a diverse group of talented volunteers</div>
      <div class="g" style="top:18px"><p>Review and align association management practices with strategic objectives and statements of Vision, Mission and Values.</p><p>Secure the ICV’s financial stability by reviewing current pricing model and practicing sound risk management.</p></div>
      <div class="a" style="top:18px"><p>Align the ICV budget and staffing needs to achieve clear strategic objectives</p><p>Utilize automation to modernize systems and administrative processes</p><p>Review and assess the relevance of current committees to determine if sufficient to meet the requirements of the strategic plan, and create new committees if deemed relevant</p></div>
    </div>
  </section>

</div>
</body>
</html>
```